Bright and beautiful business card for a coach

I'm a personal and business coach based in Perth, Australia. I need a business card that whilst subtle and elegant, will stand out and appeal on a table full of cards.

My business name is Fern Mentoring and the business card must represent the warmth and brightness implied in the name, without being gimmicky. It must have a warmth and appeal and be easy to read.

I prefer clean, minimalist designs.

It must align with the feel of my website and socials: https://www.fernmentoring-example.com.au/
https://www.instagram.com/fernmentoringau/
https://www.facebook.com/fernmentoringau
Updates

Hi Designers Thank you so much for taking the time to submit designs. I wonder if I could have explained myself a little better. Most of the designs that have been submitted look rather formal and many have quite corporate looking embellishments on them (to my eye). I would like softer, warmer, more organic. I’m open to people playing about and being more abstract, using softer embellishments (e.g the line drawing flowers and grasses I’ve used in my socials) incorporating other colours from my palette or like the social icons in my email signature (in PDF), perhaps playing with size/oversize, playing with the bleed. Please don’t be constrained by what I’ve already done, it merely needs to compliment. I’m sorry if I’m not using the right words or have led you astray. I’m no designer, but I’ve done my website, socials, email signature etc all myself (my logo was a design contest) and I was really hoping for my business card to be something more creative than I could have made with a template. Reminder: No black cards/sides please. Thank you 😊

Target Market(s)

Individuals, most likely but not all female. Creative thinkers. Likely professionals.

Industry/Entity Type

Business & Personal Coach

Contact Information for Business Card

(Fern Mentoring Logo) Name: Greta Pellham; Title: Business & Personal Coach; Phone number: +61 (0)458 913307; Email: greta@fernmentoring-example.com.au; Website: https://fernmentoring-example.com.au; Social icons for Facebook, Instagram & LinkedIn: @fernmentoringAU. Optional strapline: "A thinking partner to help you cut through the noise"

Font styles to use
Sans Serif

Colors
00AB8E
00BBA5
67D7C9
C6EFE9
E9F9F6
59FF00
82FF00
B8FF75
E3FFCB
F4FFEA
FFC000
F8CF3A
FAE287
FDF2CF
FEFAEE

Requirements
Must have
• Must align with feel of my website and socials. Must have a pop of #FFC000 (possibly whole of one side, or at least a block). Bright or white background. Easy to read.
Nice to have
• Possibly incorporate the sunshine/grass picture I have used in website and socials - will upload.
Should not have
• Must not be black or dark. Not impersonal or corporate looking.

```html
<!DOCTYPE html>
<html lang="en">
<head>
<meta charset="utf-8">
<title>Fern Mentoring – Business Card</title>
<link href="https://fonts.googleapis.com/css2?family=Allura&family=Lato:wght@300;400;700&family=Montserrat:wght@500;600&display=swap" rel="stylesheet">
<style>
  :root{
    --page:#e7e9e4;
    --sun:#ffc000;
    --white:#ffffff;
    --grass-dark:#2f4a12;
    --grass-mid:#5d8a22;
    --grass-light:#9cc24a;
    --glow:#f4c98a;
    --skin-warm:#c99a7d;
    --hair:#6b5443;
    --shirt:#2c4a5a;
  }
  *{box-sizing:border-box;margin:0;padding:0}
  html,body{width:1200px;height:1015px;overflow:hidden;background:var(--page)}
  .sheet{width:1200px;height:1015px;display:flex;flex-direction:column;align-items:center;justify-content:space-evenly}
  .card{position:relative;width:820px;height:469px;overflow:hidden;box-shadow:0 6px 20px rgba(0,0,0,.18)}
  .photo-grass{position:absolute;inset:0;
    background:
      radial-gradient(ellipse 30% 25% at 58% 8%, rgba(255,236,190,.95), rgba(244,201,138,.5) 45%, transparent 75%),
      radial-gradient(ellipse 60% 40% at 50% 15%, rgba(160,110,60,.55), transparent 70%),
      linear-gradient(180deg, #7a6a3a 0%, var(--grass-light) 30%, var(--grass-mid) 60%, var(--grass-dark) 100%);}
  /* front */
  .brand{position:absolute;left:120px;top:150px;display:flex;align-items:center;gap:14px}
  .brand-dot{width:18px;height:18px;border-radius:50%;background:var(--white)}
  .brand-name{font-family:"Lato",sans-serif;font-weight:300;font-size:46px;color:var(--white);letter-spacing:1px}
  .strap-band{position:absolute;left:0;right:0;top:350px;height:48px;background:var(--sun);
    display:flex;align-items:center;justify-content:center}
  .strap-text{font-family:"Montserrat",sans-serif;font-weight:600;font-size:19px;color:var(--white);text-transform:uppercase;letter-spacing:.2px}
  /* back */
  .back svg.portrait{position:absolute;inset:0}
  .identity{position:absolute;left:56px;top:140px}
  .person-name{font-family:"Allura",cursive;font-size:72px;color:var(--sun);line-height:1}
  .person-title{font-family:"Lato",sans-serif;font-size:25px;color:var(--white);margin-top:2px}
  .contact-list{position:absolute;left:70px;top:272px;list-style:none}
  .contact-list li{display:flex;align-items:center;gap:12px;font-family:"Lato",sans-serif;font-size:20px;color:var(--white);height:30px}
  .contact-list svg{width:20px;height:20px;flex:none}
  .socials{position:absolute;left:70px;top:378px}
  .social-dots{display:flex;gap:8px}
  .social-dots span{width:30px;height:30px;border-radius:50%;background:var(--sun)}
  .handle{font-family:"Lato",sans-serif;font-size:23px;color:var(--white);margin-top:6px}
</style>
</head>
<body>
<main class="sheet">

  <section class="card front">
    <div class="photo-grass" role="img" aria-label="Sunlit close-up of green grass with warm sunlight glow and line-drawn botanical sprigs"></div>
    <div class="brand">
      <span class="brand-dot"></span>
      <span class="brand-name">Fern Mentoring</span>
    </div>
    <div class="strap-band"><p class="strap-text">A thinking partner to help you cut through the noise</p></div>
  </section>

  <section class="card back">
    <div class="photo-grass" role="img" aria-label="Sunlit green grass background with line-drawn botanical sprigs"></div>
    <svg class="portrait" viewBox="0 0 820 469" width="820" height="469">
      <defs>
        <linearGradient id="portraitTone" x1="0" y1="0" x2="1" y2="1">
          <stop offset="0" stop-color="#c9b8a8"/>
          <stop offset=".35" stop-color="var(--hair)"/>
          <stop offset=".6" stop-color="var(--skin-warm)"/>
          <stop offset="1" stop-color="var(--shirt)"/>
        </linearGradient>
      </defs>
      <path d="M480 0 C390 80 420 200 520 262 C605 315 615 400 585 469 L820 469 L820 0 Z" fill="url(#portraitTone)" role="img" aria-label="Portrait photograph of the coach, smiling, wearing glasses"/>
      <path d="M480 0 C390 80 420 200 520 262 C605 315 615 400 585 469" fill="none" stroke="var(--white)" stroke-width="8"/>
    </svg>

    <div class="identity">
      <h1 class="person-name">Greta Pellham</h1>
      <p class="person-title">Business &amp; Personal Coach</p>
    </div>

    <ul class="contact-list">
      <li><svg viewBox="0 0 24 24"><path fill="#ffc000" d="M6.6 10.8a15 15 0 0 0 6.6 6.6l2.2-2.2a1 1 0 0 1 1-.25 11.4 11.4 0 0 0 3.6.57 1 1 0 0 1 1 1V20a1 1 0 0 1-1 1A17 17 0 0 1 3 4a1 1 0 0 1 1-1h3.5a1 1 0 0 1 1 1c0 1.25.2 2.45.57 3.57a1 1 0 0 1-.25 1z"/></svg>+61 (0)458 913307</li>
      <li><svg viewBox="0 0 24 24"><path fill="#ffc000" d="M3 5h18v14H3z"/><path fill="none" stroke="#2f4a12" stroke-width="1.6" d="M3 5l9 7 9-7"/></svg>greta@fernmentoring-example.com.au</li>
      <li><svg viewBox="0 0 24 24" fill="none" stroke="#ffc000" stroke-width="2"><circle cx="12" cy="12" r="9"/><path d="M3 12h18M12 3c3 3 3 15 0 18M12 3c-3 3-3 15 0 18"/></svg>www.fernmentoring-example.com.au</li>
    </ul>

    <div class="socials">
      <div class="social-dots"><span></span><span></span><span></span></div>
      <p class="handle">@fernmentoringAU</p>
    </div>
  </section>

</main>
</body>
</html>
```